business card - for laser marking

I need design (curve) for my business card (make with laser) size 85mm x 55mm. How it look business card with laser marking see attached picture.

color:
Background: white
text and icons black

Please include: one side
1. dominik vrabec - direktor
2. phone: +386(0)41 726 190
+386(0)580 237 61
3. info@zarezko.example
4. faecebook.com/Zarezko.Ex
5. KM-ATELJE, Dominik Vrabec s.p.
Lipova ulica 19, 1000 Ljubljana, SI
6. logo

Please include: second side
1. logo
2. www.zarezko.example
3. Lasersko graviranje
ovitki telefonov, ohišja telefonov / tablic, nakit, ure, alu vizitke, dog-tagi, kemični svinčniki, orodja, noži, vžigalniki

Industry/Entity Type

Business

Contact Information for Business Card

Please include: one side
+386(0)580 237 61
3. info@zarezko.example
6. logo

1. logo
2. www.zarezko.example
3. Lasersko graviranje

Colors
000000
ffffff

Requirements
Must have
• I need design (curve) for my business card (make with laser) size 85mm x 55mm. How it look business card with laser marking see attached picture.
• color:
• Background: white
• text and icons black
• Please include: one side
• 1. dominik vrabec - direktor
• 2. phone: +386(0)41 726 190
• +386(0)580 237 61
• 3. info@zarezko.example
• 4. faecebook.com/Zarezko.Ex
• 5. KM-ATELJE, Dominik Vrabec s.p.
• Lipova ulica 19, 1000 Ljubljana, SI
• 6. logo
• Please include: second side
• 1. logo
• 2. www.zarezko.example
• 3. Lasersko graviranje
• ovitki telefonov, ohišja telefonov / tablic, nakit, ure, alu vizitke, dog-tagi, kemični svinčniki, orodja, noži, vžigalniki

```html
<!DOCTYPE html>
<html lang="sl">
<head>
<meta charset="utf-8">
<title>Zarezko – vizitka</title>
<link rel="stylesheet" href="https://fonts.googleapis.com/css2?family=Roboto:wght@400;500;700&family=Roboto+Condensed:wght@400;700&display=swap">
<style>
  :root {
    --page: #e9e6e1;
    --card: #ffffff;
    --ink: #000000;
  }
  html, body {
    margin: 0;
    width: 1200px;
    height: 911px;
    overflow: hidden;
    background: var(--page);
    font-family: "Roboto", sans-serif;
  }
  .sheet {
    position: relative;
    width: 1200px;
    height: 911px;
  }
  .card {
    position: absolute;
    top: 280px;
    width: 540px;
    height: 350px;
    border-radius: 22px;
    background: var(--card);
    overflow: hidden;
    box-shadow: 0 10px 30px rgba(0,0,0,0.18);
  }
  .card--front { left: 40px; }
  .card--back { left: 620px; }

  .front-shape {
    position: absolute;
    inset: 0;
  }
  .front-brand {
    position: absolute;
    left: 28px;
    top: 150px;
    display: flex;
    align-items: center;
    gap: 10px;
  }
  .brand-dot {
    width: 14px;
    height: 14px;
    border-radius: 50%;
    background: var(--ink);
  }
  .brand-name {
    font-family: "Roboto", sans-serif;
    font-weight: 700;
    font-size: 34px;
    letter-spacing: 1px;
    color: var(--ink);
  }
  .holder {
    position: absolute;
    right: 34px;
    top: 38px;
    text-align: right;
    color: var(--ink);
    font-family: "Roboto Condensed", sans-serif;
  }
  .holder__name {
    font-weight: 700;
    font-size: 22px;
    letter-spacing: 0.5px;
    text-transform: uppercase;
  }
  .holder__role {
    font-size: 13px;
    letter-spacing: 1px;
    margin-top: 2px;
  }
  .contact {
    position: absolute;
    right: 34px;
    top: 140px;
    text-align: right;
    color: var(--ink);
    font-size: 13px;
    line-height: 19px;
  }
  .contact__row {
    display: flex;
    justify-content: flex-end;
    align-items: center;
    gap: 8px;
  }
  .contact__icon {
    width: 12px;
    height: 12px;
    flex: none;
  }
  .contact__gap { height: 8px; }

  .back-content {
    position: absolute;
    left: 44px;
    top: 70px;
  }
  .back-brand {
    font-weight: 700;
    font-size: 58px;
    letter-spacing: 3px;
    color: var(--ink);
    line-height: 1;
  }
  .tagline {
    margin-top: 14px;
    font-size: 16px;
    color: var(--ink);
  }
  .services {
    margin-top: 6px;
    font-size: 13px;
    line-height: 19px;
    color: var(--ink);
    max-width: 440px;
  }
  .web {
    margin-top: 22px;
    font-size: 15px;
    font-weight: 700;
    color: var(--ink);
  }
</style>
</head>
<body>
<main class="sheet">

  <section class="card card--front" aria-label="Sprednja stran vizitke">
    <svg class="front-shape" width="540" height="350" viewBox="0 0 540 350" aria-hidden="true">
      <path d="M200 0 C300 110 330 230 300 350" fill="none" stroke="var(--ink)" stroke-width="1.5"/>
      <path d="M175 6 C285 110 318 230 292 346" fill="none" stroke="var(--ink)" stroke-width="6" stroke-linecap="round"/>
    </svg>

    <div class="front-brand">
      <span class="brand-dot"></span>
      <span class="brand-name">ZAREZKO</span>
    </div>

    <div class="holder">
      <div class="holder__name">Dominik Vrabec</div>
      <div class="holder__role">DIREKTOR</div>
    </div>

    <div class="contact">
      <div>KM-ATELJE</div>
      <div>Dominik Vrabec s.p.</div>
      <div>Lipova ulica 19</div>
      <div>1000 Ljubljana, SI</div>
      <div class="contact__gap"></div>
      <div class="contact__row">+386(0)580 237 61
        <svg class="contact__icon" viewBox="0 0 12 12" aria-hidden="true"><path d="M2.5 1 L4.5 1 L5.2 3.6 L4 4.5 C4.6 5.8 6 7.3 7.5 8 L8.4 6.8 L11 7.5 L11 9.5 C11 10.3 10.3 11 9.5 11 C5 11 1 7 1 2.5 C1 1.7 1.7 1 2.5 1 Z" fill="var(--ink)"/></svg>
      </div>
      <div class="contact__row">+386(0)41 726 190
        <svg class="contact__icon" viewBox="0 0 12 12" aria-hidden="true"><rect x="3" y="0.5" width="6" height="11" rx="1" fill="none" stroke="var(--ink)" stroke-width="1.2"/><circle cx="6" cy="9.6" r="0.7" fill="var(--ink)"/></svg>
      </div>
      <div class="contact__row">info@zarezko.example
        <svg class="contact__icon" viewBox="0 0 12 12" aria-hidden="true"><rect x="0.8" y="2.5" width="10.4" height="7" fill="none" stroke="var(--ink)" stroke-width="1.2"/><path d="M1 3 L6 7 L11 3" fill="none" stroke="var(--ink)" stroke-width="1.2"/></svg>
      </div>
      <div class="contact__row">faecebook.com/Zarezko.Ex
        <svg class="contact__icon" viewBox="0 0 12 12" aria-hidden="true"><rect x="1" y="1" width="10" height="10" rx="1.5" fill="var(--ink)"/></svg>
      </div>
    </div>
  </section>

  <section class="card card--back" aria-label="Zadnja stran vizitke">
    <div class="back-content">
      <div class="back-brand">ZAREZKO</div>
      <div class="tagline">Lasersko graviranje</div>
      <div class="services">ovitki telefonov, ohišja telefonov / tablic, nakit, ure, alu vizitke, dog-tagi, kemični svinčniki, orodja, noži, vžigalniki</div>
      <div class="web">www.zarezko.example</div>
    </div>
  </section>

</main>
</body>
</html>
```